Business Card for a Life Coaching Company

MOSSVALE is a Life Coaching company that was initiated to support people who want to transform thier life or ana aspect of it.
our slogan is : "Dream. Believe. Succeed"
our logo is uploaded.
The name of the company implies that leadership, strength and wisdom required to change your life.
We want an attractive business card that would give an impression of reliability, support and change. so we really want it unique. Here are some examples of unique cards:

http://www.pixelharbornotes.example/2009/05/100-really-creative-business-cards/

MossVale is a life coaching organization focusing on individual transformation through the application of relevant and timeless principles of success.  MossVale believes that real, sustainable life transformations are brought about by tuning into the timeless wisdom we each carry in our hearts while boldy acting in the direction of our dreams.

Contacts on the card:
Address: 7 Tarek Ibn Nabil Rosefield Amber Coast
Tel: +202 24 81 37 52
Fax: +202 24 81 37 19
Mobile: +2 012 574 9026 (Nadia Sherif)
+2 0199915815 (Kamal Rashidi)

By the way, our temporary website is http://www.mossvale.example

We have attached an .eps file with various configurations of our logo.

```html
<!DOCTYPE html>
<html lang="en">
<head>
<meta charset="utf-8">
<title>MossVale Business Card</title>
<link rel="stylesheet" href="https://fonts.googleapis.com/css2?family=Cinzel:wght@400&family=Tinos:wght@400;700&display=swap">
<style>
  :root {
    --page: #ffffff;
    --card: #2b2b2b;
    --gold: #e58d1f;
    --gold-deep: #b9640f;
    --gold-soft: #f0a238;
    --label: #cfcfcf;
  }
  html, body {
    margin: 0;
    padding: 0;
    width: 1200px;
    height: 840px;
    overflow: hidden;
    background: var(--page);
  }
  .canvas {
    position: relative;
    width: 1200px;
    height: 840px;
  }
  .card {
    position: absolute;
    width: 450px;
    height: 270px;
    background: var(--card);
    overflow: hidden;
  }
  .card--front { left: 136px; top: 227px; }
  .card--back { left: 605px; top: 226px; }

  .brand-mark {
    position: absolute;
    left: 14px;
    top: 27px;
    width: 200px;
    height: 220px;
  }
  .brand-name {
    position: absolute;
    left: 220px;
    top: 14px;
    margin: 0;
    font-family: "Cinzel", serif;
    font-weight: 400;
    font-size: 74px;
    line-height: 80px;
    color: var(--gold);
    letter-spacing: 0;
  }
  .brand-name span { display: block; }
  .web {
    position: absolute;
    font-family: "Cinzel", serif;
    font-size: 14px;
    letter-spacing: 3.4px;
    color: var(--gold);
    margin: 0;
    white-space: nowrap;
  }
  .card--front .web { left: 220px; top: 193px; }
  .card--back .web { left: 28px; top: 58px; letter-spacing: 6px; }

  .contacts {
    position: absolute;
    left: 28px;
    top: 88px;
    margin: 0;
    padding: 0;
    list-style: none;
    font-family: "Tinos", serif;
    font-size: 15px;
    line-height: 19px;
    color: var(--label);
    white-space: nowrap;
  }
  .contacts li:nth-child(2),
  .contacts li:nth-child(3) { margin-top: 2px; }
  .contacts .value { color: var(--gold-soft); }
  .contacts .value--strong { font-weight: 700; }

  .lion-art {
    position: absolute;
    right: 0;
    top: 0;
    width: 142px;
    height: 270px;
  }
</style>
</head>
<body>
<main class="canvas">
  <section class="card card--front" aria-label="Card front">
    <svg class="brand-mark" viewBox="0 0 200 220" aria-hidden="true">
      <defs>
        <linearGradient id="markGold" x1="0" y1="0" x2="1" y2="1">
          <stop offset="0" stop-color="#f0a238"/>
          <stop offset="1" stop-color="#b9640f"/>
        </linearGradient>
      </defs>
      <circle cx="100" cy="110" r="96" fill="url(#markGold)"/>
    </svg>
    <h1 class="brand-name"><span>MOSS</span><span>VALE</span></h1>
    <p class="web">WWW.MOSSVALE.COM</p>
  </section>

  <section class="card card--back" aria-label="Card back">
    <p class="web">WWW.MOSSVALE.COM</p>
    <ul class="contacts">
      <li>Tel: <span class="value">+202 24 81 37 52</span></li>
      <li>Fax: <span class="value">+202 24 81 37 19</span></li>
      <li>Mobile: (Nadia Sherif) <span class="value">+2 012 574 9026</span></li>
      <li>Address: <span class="value">7 Tarek Ibn Nabil</span></li>
      <li><span class="value value--strong">Rosefield Amber Coast</span></li>
    </ul>
    <svg class="lion-art" viewBox="0 0 142 270" role="img" aria-label="Large gold lion head decoration in profile">
      <defs>
        <linearGradient id="artGold" x1="0" y1="0" x2="1" y2="1">
          <stop offset="0" stop-color="#e58d1f" stop-opacity="0.15"/>
          <stop offset="0.5" stop-color="#d47a18" stop-opacity="0.55"/>
          <stop offset="1" stop-color="#b9640f" stop-opacity="0.35"/>
        </linearGradient>
      </defs>
      <rect x="0" y="0" width="142" height="270" fill="url(#artGold)"/>
    </svg>
  </section>
</main>
</body>
</html>
```